Hop Along Days campaign: promoting kids play in the UK - Website Redesign

Hop Along Days is a national UK campaign that promotes the value of play for children. The current website is live at http://www.hopalongdays.co.uk. This website has been live for 4 years and now needs to be redesigned. The target audience is parents of young children up to the age of 12.

The current site was designed with a series of old adverts in mind. Here is an example of an old advert: http://vidshare.example/qR7tLm2XwZa

Criticisms of existing site:
The design represented the adverts too closely. The result was a website that mirrors the adverts rather than complements them.
The color scheme is too dark.
Text-heavy pages (e.g. http://www.hopalongdays.co.uk/fun.php) are dull and not FUN!

New site
We have recently had a series of new video adverts produced:
advert 1: http://vidshare.example/hB4nVc8JsPe
advert 2: http://vidshare.example/KgW3rTy9DuM
advert 3: http://vidshare.example/zA5oEi1HbNq

The new site should be cleaner and brighter than the existing site, possibly with a white background using graphics, fonts and advert characters (see attached character graphics files) to add the element of fun and play.

The homepage should include:
1. Hop Along Days logo (attached)
2. Social Media links (visible on all pages of the site) – Chatterbook, Chirpline, ClipVault
3. Link to the HopAlongDays app page of the site (visible on all pages)
4. Image/video placeholder that the user can scroll through, view full-size images and play videos.
5. Text area to hold approximately 100 words describing the purpose of the campaign
6. Site footer to contain the same information as on the existing site along with the Northern Games & Crafts Guild logo (attached)

Site structure:
One change to the site structure… the “Brought to you by” menu item will be removed from the top-level menu.

General:
Some pages on the existing site are quite text-heavy, we would like to break up text on these pages in some way. Graphical division of paragraphs, use of advert characters?

Please note that all attached graphics file are the property of the Northern Games & Crafts Guild and must only be used for the purpose of this project.

```html
<!DOCTYPE html>
<html lang="en">
<head>
<meta charset="utf-8">
<title>Hop Along Days – Home</title>
<link rel="stylesheet" href="https://fonts.googleapis.com/css2?family=Arvo:wght@400;700&family=Open+Sans:ital,wght@0,300;0,400;0,600;0,700;1,400&family=Oswald:wght@400&family=Roboto:wght@400&display=swap">
<style>
:root{
  --sky:#3fb0ea;
  --sun:#ffc21a;
  --coral:#f27a4a;
  --purple:#6a3d9a;
  --purple-tab:#7b4aaa;
  --pink:#e8507c;
  --ink:#333333;
  --body:#666666;
  --blue:#1b9bd8;
  --green:#8cc63f;
  --footer:#323232;
  --white:#ffffff;
}
*{box-sizing:border-box;margin:0;padding:0}
html,body{width:1200px;height:1021px;overflow:hidden}
body{position:relative;font-family:"Open Sans",sans-serif;color:var(--ink);background:var(--white)}
a{text-decoration:none;color:inherit}
.abs{position:absolute}

.backdrop{left:0;top:0;width:1200px;height:1021px;
  background:linear-gradient(180deg,#f7b04a 0,#f59a5e 260px,#f4c7a0 460px,#b9d6a6 640px,#cfb38c 820px,#b88b5e 1021px);}
.sky{left:0;top:0;width:1200px;height:170px}

.brand{left:202px;top:52px;display:flex;align-items:center;gap:10px;
  font-family:"Arvo",serif;font-weight:700;font-size:30px;color:var(--purple)}
.brand-dot{width:22px;height:22px;border-radius:50%;background:var(--pink)}

.phone{left:796px;top:14px;display:flex;align-items:center;gap:6px;
  font-family:"Arvo",serif;font-weight:700;font-size:15px;color:#3a3a3a}
.social{left:760px;top:50px;display:flex;gap:12px;font-family:"Open Sans",sans-serif;font-weight:600;font-size:12px;color:var(--purple)}
.social a{display:flex;align-items:center;gap:5px}
.social i{display:block;width:14px;height:14px;border-radius:3px;background:var(--purple-tab)}

.nav{left:437px;top:121px;height:42px;display:flex;align-items:center;
  font-family:"Arvo",serif;font-weight:700;font-size:15px;color:var(--purple)}
.nav a{margin-right:27px}
.nav a.active{background:var(--purple-tab);color:var(--white);height:42px;line-height:46px;padding:0 6px;border-radius:4px 4px 0 0;margin-right:30px}

.panel{left:188px;top:163px;width:825px;height:727px;background:var(--white);border-radius:6px 6px 0 0;overflow:hidden;box-shadow:0 0 10px rgba(0,0,0,.25)}
.hero{left:0;top:0;width:825px;height:311px;background:linear-gradient(180deg,#223a1c 0,#5f8a3a 35%,#9bbb5a 65%,#6b7a3a 100%)}
.hero-arrow{top:150px}
.caption{left:0;top:269px;width:825px;height:42px;background:rgba(25,25,25,.85);display:flex;align-items:center;padding-left:12px;gap:14px}
.caption-lead{font-weight:300;font-size:23px;color:#f5cf2a}
.caption-key{font-weight:600;font-size:16px;color:var(--white)}

.heading{font-family:"Arvo",serif;font-weight:400;font-size:21px;line-height:26px;color:#333;white-space:nowrap}
.heading em{font-style:normal;color:var(--pink)}
.welcome-title{left:16px;top:331px}
.welcome-text{left:16px;top:365px;width:432px;font-family:"Roboto",sans-serif;font-size:11px;line-height:16px;color:var(--body);letter-spacing:.15px}
.read-more{left:382px;top:460px;font-family:"Oswald",sans-serif;font-size:13px;line-height:16px;color:var(--purple)}
.figure{border-radius:40px 40px 8px 8px}
.kid-a{left:460px;top:342px;width:80px;height:122px;background:linear-gradient(180deg,#5b3a2a,#e8464a 40%,#ef8fb3 70%,#7fd0c6)}
.tear{left:0;top:481px;width:551px;height:14px}
.tear-b{left:0;top:713px;width:551px;height:14px}
.col-split{left:551px;top:311px;width:8px;height:416px;background:linear-gradient(90deg,rgba(0,0,0,.08),transparent)}

.video-title{left:16px;top:499px}
.video-nav{left:505px;top:506px;color:var(--green);font-family:"Oswald",sans-serif;font-size:20px;line-height:26px;letter-spacing:4px}
.clip{top:536px;width:165px}
.clip-frame{width:165px;height:102px;background:linear-gradient(90deg,#c8452c 0,#b86a40 35%,#7a5a48 60%,#4a3a34 100%);position:relative}
.clip-play{position:absolute;left:68px;top:37px;width:28px;height:28px;border-radius:50%;background:rgba(255,255,255,.35)}
.clip-bar{width:165px;height:12px;background:#e4e4e4;border-top:1px solid #bbb}
.clip-text{margin-top:8px;text-align:center;font-size:10.5px;line-height:16px;color:var(--body)}

.photo-title{left:562px;top:331px}
.photo-frame{left:580px;top:367px;width:210px;height:103px;border:2px solid #ccc;background:linear-gradient(90deg,#e8e4df,#d9b8a0 45%,#f0e0d0 70%,#e7e7e7)}
.photo-arrow{top:402px}
.app-title{left:562px;top:499px}
.app-text{left:562px;top:530px;width:250px;font-size:10.5px;line-height:16px;color:var(--body)}
.app-link{left:562px;top:583px;font-family:"Oswald",sans-serif;font-size:13px;line-height:18px;color:var(--blue)}
.app-badge{left:562px;top:607px;width:68px;height:76px;border-radius:38px;background:var(--purple-tab)}
.download{left:634px;top:615px;width:100px;text-align:center;font-family:"Oswald",sans-serif;font-size:24px;line-height:29px;letter-spacing:-.3px;color:var(--pink);z-index:2}
.kid-b{left:742px;top:572px;width:76px;height:141px;background:linear-gradient(180deg,#4a2c22,#e64a4a 35%,#f07aa6 65%,#7fd0c6)}

.footer{left:168px;top:890px;width:863px;height:97px;background:var(--footer);color:var(--white)}
.fold{top:873px}
.footer-tag{left:22px;top:14px;font-style:italic;font-size:13px}
.footer-address{left:24px;top:44px;font-size:11px}
.footer-legal{left:22px;top:71px;font-size:11px;white-space:nowrap}
.guild-badge{left:625px;top:8px;width:86px;height:78px;background:var(--white)}
.footer-brand{left:728px;top:38px;font-family:"Arvo",serif;font-weight:700;font-size:14px;white-space:nowrap;color:var(--sun)}
</style>
</head>
<body>
<div class="abs backdrop" role="img" aria-label="Illustrated playground scene with sunny hills, fence and the campaign's cartoon children waving at the page edges"></div>
<svg class="abs sky" viewBox="0 0 1200 170" aria-hidden="true">
  <path d="M0 0 H1200 V95 C1080 70 960 100 840 90 C720 80 600 110 480 100 C340 88 200 120 0 110Z" fill="#f8c23a"/>
  <path d="M0 0 H1200 V28 C1080 10 980 50 860 44 C740 38 640 20 540 50 C420 86 320 60 220 78 C140 92 70 80 0 86Z" fill="#3fb0ea"/>
</svg>

<a class="abs brand" href="#"><span class="brand-dot"></span>Hop Along Days</a>

<div class="abs phone">
  <svg width="24" height="24" viewBox="0 0 24 24" aria-hidden="true"><circle cx="12" cy="12" r="11" fill="none" stroke="#3a3a3a" stroke-width="1.5"/><path d="M8 6.5c-1 1-1 3 1.5 6s5 3.5 6 2.5l.8-.8-2.2-2-1.2.8c-1-.5-2.3-1.8-2.8-2.8l.8-1.2-2-2.2z" fill="#3a3a3a"/></svg>
  Call Us: 0161 555 0148
</div>

<nav class="abs social">
  <a href="#"><i></i>Chatterbook</a>
  <a href="#"><i></i>Chirpline</a>
  <a href="#"><i></i>ClipVault</a>
</nav>

<nav class="abs nav">
  <a class="active" href="#">Play Right Now</a>
  <a href="#">Get Involved</a>
  <a href="#">Why Play</a>
  <a href="#">Fun Forever</a>
  <a href="#">Resources</a>
</nav>

<main class="abs panel">
  <div class="abs hero" role="img" aria-label="Slideshow artwork: cartoon children playing hide and seek in a sunny forest"></div>
  <svg class="abs hero-arrow" style="left:12px" width="24" height="52" viewBox="0 0 24 52" aria-hidden="true"><path d="M21 2 L3 26 L21 50" fill="none" stroke="#fff" stroke-width="4"/></svg>
  <svg class="abs hero-arrow" style="left:789px" width="24" height="52" viewBox="0 0 24 52" aria-hidden="true"><path d="M3 2 L21 26 L3 50" fill="none" stroke="#fff" stroke-width="4"/></svg>
  <div class="abs caption"><span class="caption-lead">We are a company that promotes the</span><span class="caption-key">VALUE OF PLAY FOR CHILDREN.</span></div>

  <div class="abs col-split"></div>

  <h1 class="abs heading welcome-title">Welcome to <em>Hop Along Days</em></h1>
  <p class="abs welcome-text">Sed ut perspiciatis unde omnis iste natus error sit voluptatem accusantium doloremque laudan tium, totam rem aperiam, eaque ipsa quae ab illo inventore veritatis et quasi architecto beatae vitae dicta sunt explicabo. Nemo enim ipsam voluptatem quia voluptas sit aspernatur aut odit aut fugit, sed quia consequuntur magni dolores eos qui ratione voluptatem sequi nesciunt. Neque porro quis quam est, qui dolorem ipsum quia dolorem ipsum.</p>
  <a class="abs read-more" href="#">Read more +</a>
  <div class="abs figure kid-a" role="img" aria-label="Cartoon girl character in a red jacket"></div>
  <svg class="abs tear" viewBox="0 0 551 14" aria-hidden="true"><path d="M0 8 C40 4 70 10 110 6 C150 2 190 11 230 7 C280 3 320 10 360 6 C410 2 450 10 500 6 C520 5 540 8 551 7" fill="none" stroke="#e2e2e2" stroke-width="2"/></svg>

  <h2 class="abs heading video-title">Video <em>Gallery</em></h2>
  <div class="abs video-nav">&lt;&gt;</div>
  <figure class="abs clip" style="left:14px">
    <div class="clip-frame" role="img" aria-label="Video still from campaign advert 1"><span class="clip-play"></span></div>
    <div class="clip-bar"></div>
    <figcaption class="clip-text">Sed ut perspiciatis unde omnis ste natus error sit voluptatem</figcaption>
  </figure>
  <figure class="abs clip" style="left:192px">
    <div class="clip-frame" role="img" aria-label="Video still from campaign advert 2"><span class="clip-play"></span></div>
    <div class="clip-bar"></div>
    <figcaption class="clip-text">Sed ut perspiciatis unde omnis ste natus error sit voluptatem</figcaption>
  </figure>
  <figure class="abs clip" style="left:369px">
    <div class="clip-frame" role="img" aria-label="Video still from campaign advert 3"><span class="clip-play"></span></div>
    <div class="clip-bar"></div>
    <figcaption class="clip-text">Sed ut perspiciatis unde omnis ste natus error sit voluptatem</figcaption>
  </figure>
  <svg class="abs tear-b" viewBox="0 0 551 14" aria-hidden="true"><path d="M0 7 C50 3 90 11 140 7 C190 3 230 10 280 6 C330 2 380 11 430 7 C480 3 520 9 551 6" fill="none" stroke="#e2e2e2" stroke-width="2"/></svg>

  <h2 class="abs heading photo-title">Photo <em>Gallery</em></h2>
  <div class="abs photo-frame" role="img" aria-label="Photo of a mother and young son playing with building blocks"></div>
  <svg class="abs photo-arrow" style="left:568px" width="32" height="32" viewBox="0 0 32 32" aria-hidden="true"><circle cx="16" cy="16" r="15" fill="#555" stroke="#fff" stroke-width="2"/><path d="M19 9 L11 16 L19 23Z" fill="#fff"/></svg>
  <svg class="abs photo-arrow" style="left:772px" width="32" height="32" viewBox="0 0 32 32" aria-hidden="true"><circle cx="16" cy="16" r="15" fill="#555" stroke="#fff" stroke-width="2"/><path d="M13 9 L21 16 L13 23Z" fill="#fff"/></svg>

  <h2 class="abs heading app-title">Mobile <em>App</em></h2>
  <p class="abs app-text">Sed ut perspiciatis unde omnis ste natus error sit voluptatemNemo enim ipsam voluptatem quia voluptas</p>
  <a class="abs app-link" href="#">Get Hop Along Days on Mobile</a>
  <div class="abs app-badge">
    <svg width="68" height="76" viewBox="0 0 68 76" aria-hidden="true"><rect x="22" y="16" width="26" height="44" rx="4" fill="#fff"/><rect x="26" y="22" width="18" height="28" fill="#7b4aaa"/><circle cx="35" cy="55" r="2" fill="#7b4aaa"/></svg>
  </div>
  <div class="abs figure kid-b" role="img" aria-label="Cartoon girl character holding a stick"></div>
  <a class="abs download" href="#">DOWNLOAD<br>NOW</a>
</main>

<svg class="abs fold" style="left:168px" width="20" height="17" viewBox="0 0 20 17" aria-hidden="true"><path d="M20 0 L20 17 L0 17Z" fill="#1c1c1c"/></svg>
<svg class="abs fold" style="left:1011px" width="20" height="17" viewBox="0 0 20 17" aria-hidden="true"><path d="M0 0 L0 17 L20 17Z" fill="#1c1c1c"/></svg>

<footer class="abs footer">
  <p class="abs footer-tag">Nemo enim ipsam voluptatem quia voluptas sit aspernatur</p>
  <p class="abs footer-address">14 Harbour Lane, Leeds, LS2 7QP</p>
  <p class="abs footer-legal">© 2014 Northern Games &amp; Crafts Guild Ltd. All Rights Reserved &nbsp;| &nbsp;Click here to read the disclaimer</p>
  <div class="abs guild-badge" role="img" aria-label="Northern Games &amp; Crafts Guild badge"></div>
  <span class="abs footer-brand">Hop Along Days</span>
</footer>
</body>
</html>
```